Brightline Energy Product Distribution Brochure

We are looking to have our current brochure for our customers completely redesigned...the idea is to present the relevant information in an attractive way . Our website is brightlineenergyco.example where you can find more information about us. We have included a file with a rough idea of the page order and what each should include but feel free to adapt based on design. The example provided is only for context and doesnt have to be maintained. We will be using the brochure both digitally and in print form. As long as it reads easily and is eye catching, the design can be horizontal or vertical.Final deliverable should be indesign file.

"Our Brands" page: should be limited to one page (space being enough) where it has the header for each one (for example diesel generators) space for one or two lines of text and then the corresponding logos for each of the five categories
Updates

For those asking: the "our brands" page should be a single page layout where there is a header with the corresponding section and space for maybe one line of text followed by the two logos for that category. Each of the product pages should be similar in fashion to the one in the document attached: a photo of the product with some white space and space for the text to be included. We will be posting additional examples today

Target Market(s)

We want to present it to customers both digitally and in print so they can see our products

Industry/Entity Type

Power Generation

Font styles to use
Serif

Requirements
Must have
• Eye catching and able to present the information in a presentable fashion. Rest is up to you.
Nice to have
• Should incorporate the colors of our logo but can also add other depending on design

```html
<!DOCTYPE html>
<html lang="en">
<head>
<meta charset="utf-8">
<title>Brightline Energy – Product Brochure Spread</title>
<link rel="stylesheet" href="https://fonts.googleapis.com/css2?family=Montserrat:wght@400;500;600;900&display=swap">
<style>
  :root {
    --backdrop-light: #d1d2d4;
    --backdrop-dark: #8b8c8e;
    --brand-yellow: #fbbf0f;
    --bright-yellow: #f7e23a;
    --charcoal: #3d3a3b;
    --ink: #1e1e1e;
    --paper: #ffffff;
  }
  * { margin: 0; padding: 0; box-sizing: border-box; }
  html, body { width: 1200px; height: 801px; overflow: hidden; }
  body {
    position: relative;
    background: var(--backdrop-light);
    font-family: "Montserrat", Arial, sans-serif;
    color: var(--ink);
  }
  .backdrop { position: absolute; inset: 0; }
  .spread {
    position: absolute; left: 79px; top: 80px; width: 1034px; height: 668px;
    overflow: hidden;
  }
  .page { position: absolute; top: 0; height: 668px; }
  .page--left { left: 0; width: 517px; }
  .page--right { left: 517px; width: 517px; }
  .photo { position: absolute; inset: 0; }
  .photo--gears { background: linear-gradient(135deg, #4a4746 0%, #7c6a5c 40%, #b4aca5 70%, #5f574f 100%); }
  .photo--plant { background: linear-gradient(180deg, #1f2a3a 0%, #3c3f44 35%, #7b5a2b 65%, #3f2a16 100%); }
  .yellow-wedge { position: absolute; inset: 0; }

  .eyebrow {
    position: absolute; top: 49px; font-size: 23px; line-height: 1; font-weight: 500;
    color: var(--paper); letter-spacing: 0.4px; white-space: nowrap;
  }
  .eyebrow::after {
    content: ""; position: absolute; left: 0; top: 30px; width: 46px; height: 4px;
    background: var(--brand-yellow);
  }
  .page-title {
    position: absolute; top: 86px; font-size: 34px; line-height: 1; font-weight: 900;
    color: var(--brand-yellow); letter-spacing: 0.3px; white-space: nowrap;
  }
  .section-label {
    position: absolute; font-size: 15px; line-height: 1; font-weight: 400;
    color: var(--brand-yellow); letter-spacing: 0.3px;
  }

  .product-card { position: absolute; top: 182px; width: 229px; height: 393px; background: var(--paper); }
  .product-photo { position: absolute; }
  .product-name {
    position: absolute; left: 37px; top: 84px; font-size: 19px; font-weight: 500;
    line-height: 25px; color: var(--brand-yellow); letter-spacing: 0.6px;
  }
  .body-copy { font-size: 8.6px; line-height: 11.1px; color: var(--ink); }
  .product-card .body-copy { position: absolute; left: 37px; top: 148px; width: 154px; }

  .description-panel { position: absolute; left: 36px; top: 230px; width: 481px; height: 309px; background: var(--paper); }
  .description-panel .body-copy--col1 { position: absolute; left: 19px; top: 22px; width: 166px; }
  .description-panel .body-copy--col2 { position: absolute; left: 222px; top: 106px; width: 222px; }
  .controller-photo {
    position: absolute; left: 251px; top: 153px; width: 219px; height: 164px;
    border-radius: 6px; background: linear-gradient(180deg, #2a2a2c 0%, #161617 100%);
  }
  .partner-mark {
    position: absolute; left: 383px; top: 221px; width: 54px; height: 54px;
    background: #000; display: flex; align-items: center; justify-content: center;
    color: var(--paper); font-size: 13px; font-weight: 600;
  }

  .chevrons { position: absolute; inset: 0; pointer-events: none; }
  .page-number {
    position: absolute; top: 630px; width: 84px; height: 38px;
    background: var(--brand-yellow);
    clip-path: polygon(0 100%, 0 30%, 22% 0, 100% 0, 72% 100%);
    font-size: 21px; font-weight: 900; color: var(--ink);
    padding: 7px 0 0 30px;
  }
</style>
</head>
<body>
  <svg class="backdrop" width="1200" height="801" aria-hidden="true">
    <polygon points="0,616 1200,323 1200,801 0,801" fill="var(--backdrop-dark)"/>
  </svg>

  <main class="spread">
    <section class="page page--left">
      <div class="photo photo--gears" role="img" aria-label="Close-up photograph of machined gears and alternator components"></div>

      <p class="eyebrow" style="left:37px">OUR PRODUCT</p>
      <h1 class="page-title" style="left:37px">ALTERNATOR PARTS</h1>
      <p class="section-label" style="left:38px;top:146px">FEATURES</p>

      <article class="product-card" style="left:0">
        <div class="product-photo" role="img" aria-label="Automatic voltage regulator circuit board" style="left:126px;top:-46px;width:114px;height:132px;background:linear-gradient(135deg,#2b3442,#101418);transform:rotate(-8deg)"></div>
        <h2 class="product-name">PRODUCT<br>NAME</h2>
        <p class="body-copy">Lorem ipsum dolor sit amet, consectetuer adipiscing elit, sed diam nonummy nibh euismod tincidunt ut laoreet dolore magna aliquam erat volutpat. Ut wisi enim ad minim veniam, quis nostrud exerci tation ullamcorper suscipit lobortis nisl ut aliquip ex ea commodo consequat. Duis autem vel eum iriure dolor in hendrerit in vulputate velit esse molestie consequat, vel illum dolore eu feugiat nulla facilisis at vero eros et accumsan et iusto odio dignissim qui blandit praesent luptatum zzril delenit augue duis dolore te feugait nulla facilisi.</p>
      </article>

      <article class="product-card" style="left:254px">
        <div class="product-photo" role="img" aria-label="Current boost system module in a silver metal housing" style="left:48px;top:-40px;width:131px;height:114px;background:linear-gradient(135deg,#f2f2f2,#a9abad)"></div>
        <h2 class="product-name" style="left:36px">PRODUCT<br>NAME</h2>
        <p class="body-copy" style="left:36px">Lorem ipsum dolor sit amet, consectetuer adipiscing elit, sed diam nonummy nibh euismod tincidunt ut laoreet dolore magna aliquam erat volutpat. Ut wisi enim ad minim veniam, quis nostrud exerci tation ullamcorper suscipit lobortis nisl ut aliquip ex ea commodo consequat. Duis autem vel eum iriure dolor in hendrerit in vulputate velit esse molestie consequat, vel illum dolore eu feugiat nulla facilisis at vero eros et accumsan et iusto odio dignissim qui blandit praesent luptatum zzril delenit augue duis dolore te feugait nulla facilisi.</p>
      </article>
    </section>

    <section class="page page--right">
      <div class="photo photo--plant" role="img" aria-label="Industrial power plant with towers and pipework at dusk"></div>
      <svg class="yellow-wedge" width="517" height="668" aria-hidden="true">
        <polygon points="190,231 517,63 517,231" fill="var(--bright-yellow)"/>
      </svg>

      <p class="eyebrow" style="left:36px">OUR PRODUCT</p>
      <h1 class="page-title" style="left:36px">CONTROLLERS</h1>
      <p class="section-label" style="left:36px;top:199px">DESCRIPTION</p>

      <div class="description-panel">
        <p class="body-copy body-copy--col1">Lorem ipsum dolor sit amet, consectetuer adipiscing elit, sed diam nonummy nibh euismod tincidunt ut laoreet dolore magna aliquam erat volutpat. Ut wisi enim ad minim veniam, quis nostrud exerci tation ullamcorper suscipit lobortis nisl ut aliquip ex ea commodo consequat. Duis autem vel eum iriure dolor in hendrerit in vulputate velit esse molestie consequat, vel illum dolore eu feugiat nulla facilisis at vero eros et accumsan et iusto odio dignissim qui blandit praesent luptatum zzril delenit augue duis dolore te feugait nulla facilisi.</p>
        <p class="body-copy body-copy--col2">Lorem ipsum dolor sit amet, consectetuer adipiscing elit, sed diam nonummy nibh euismod tincidunt ut laoreet dolore magna aliquam erat volutpat. Ut wisi enim ad minim veniam, quis nostrud exerci tation ullamcorper suscipit lobortis nisl ut aliquip ex ea commodo consequat. Duis autem vel eum iriure dolor in hendrerit in vulputate velit esse molestie consequat.</p>
        <div class="partner-mark">NCS</div>
      </div>
      <div class="controller-photo" role="img" aria-label="Generator control module with display screen and push buttons"></div>
    </section>

    <svg class="chevrons" width="1034" height="668" aria-hidden="true">
      <polyline points="335,680 684,456 1045,650" fill="none" stroke="var(--brand-yellow)" stroke-width="15"/>
      <polyline points="445,680 757,469 1045,603" fill="none" stroke="var(--charcoal)" stroke-width="12"/>
    </svg>

    <div class="page-number" style="left:0">10</div>
    <div class="page-number" style="left:517px">11</div>
  </main>
</body>
</html>
```